Brand new redesign of Brightpath finance website

I need a new website design that i can advertise a great low interest rate on the front page and capture input application details that will send through to my email address.

some car finance companies will be similar to this would be listed below

tallowcredit.example.com.au
mirabelfinance.example.com.au
finance725.example.com.au
quenbyfinance.example.com.au
finance91.example.com.au

Reason: I have changed the project to a committed project. all the webpages should have the same format just different content and i want to be able to edit the front page easily to update my interest rates.

Target Market(s)

Australian Finance market targeting a younger demographic

Industry/Entity Type

Finance

Coding

Coded - Design and coding required

Number of Pages Required

5+ page

Font styles to use
Serif
Sans Serif

Colors
0255a3
ffffff
cedeed

Requirements
Must have
• application capture form
• apply now buttons
• Headline rate front page

```html
<!DOCTYPE html>
<html lang="en">
<head>
<meta charset="utf-8">
<title>Brightpath Finance – Vehicle Finance</title>
<link rel="stylesheet" href="https://fonts.googleapis.com/css2?family=Lato:ital,wght@0,400;0,700;0,900;1,400&family=Questrial&display=swap">
<style>
:root{
  --brand:#0255a3;
  --brand-dark:#01417d;
  --pale:#cedeed;
  --white:#ffffff;
  --ink:#2b2b2b;
  --muted:#555555;
  --paper:#f1f1f1;
  --night:#222222;
}
*{box-sizing:border-box;margin:0;padding:0}
html,body{width:1200px;height:2228px;overflow:hidden}
body{position:relative;font-family:"Lato",sans-serif;color:var(--ink);background:var(--white)}
.abs{position:absolute}

/* header */
.site-header{position:absolute;left:0;top:0;width:1200px;height:88px;background:var(--white);border-top:3px solid #d8d8d8}
.brand{position:absolute;left:161px;top:22px;display:flex;align-items:center;gap:12px}
.brand-mark{width:40px;height:40px;border-radius:50%;background:var(--brand)}
.brand-name{font-weight:900;font-size:28px;color:var(--brand);letter-spacing:.5px}
.btn-apply{position:absolute;left:745px;top:32px;width:116px;height:30px;background:var(--brand);color:var(--white);font-weight:900;font-size:11px;letter-spacing:.5px;display:flex;align-items:center;justify-content:center;border-left:3px solid var(--night);border-right:3px solid var(--night)}
.header-phone{position:absolute;left:890px;top:32px;display:flex;align-items:center;gap:10px;font-weight:700;font-size:19px;color:var(--brand)}

/* nav */
.main-nav{position:absolute;left:0;top:88px;width:1200px;height:46px;background:var(--brand)}
.main-nav ul{list-style:none;display:flex;position:absolute;left:161px;top:0;height:46px}
.main-nav li{height:46px;display:flex;align-items:center;padding:0 16px;color:var(--white);font-size:14px;text-transform:uppercase}
.main-nav li.is-active{background:var(--pale);color:var(--ink);padding:0 24px}

/* hero */
.hero-photo{position:absolute;left:0;top:134px;width:1200px;height:509px;background:linear-gradient(100deg,#c7b9a6 0%,#e6ddd2 30%,#b8b1a6 55%,#8c968c 80%,#6f8a6a 100%)}
.rate-seal{position:absolute;left:160px;top:440px;width:186px;height:186px;border-radius:50%;border:5px solid rgba(255,255,255,.55)}
.feature-list{position:absolute;left:374px;top:463px;width:338px;list-style:none}
.feature-list li{background:rgba(206,222,237,.92);margin-bottom:4px;border-radius:3px;padding:6px 10px 6px 36px;font-size:15px;text-transform:uppercase;position:relative;line-height:26px}
.feature-list svg{position:absolute;left:8px;top:10px}

.quote-panel{position:absolute;left:741px;top:134px;width:298px;height:509px;background:rgba(214,228,240,.96)}
.quote-title{position:absolute;left:16px;top:37px;width:265px;height:37px;background:var(--brand);color:var(--white);font-size:17px;display:flex;align-items:center;justify-content:center}
.quote-field{position:absolute;left:16px;width:265px;height:38px;background:var(--white);font-size:12.5px;font-style:italic;color:#444;padding:12px 8px}
.quote-terms{position:absolute;left:16px;top:382px;font-size:13px;color:#444;display:flex;align-items:center;gap:7px}
.quote-terms span.box{width:10px;height:10px;border:1px solid #888;background:var(--white)}
.quote-terms em{font-style:normal;color:var(--brand)}
.btn-quote{position:absolute;left:24px;top:418px;width:252px;height:50px;background:var(--brand);color:var(--white);font-weight:900;font-size:17px;display:flex;align-items:center;justify-content:center;border-left:3px solid var(--night);border-right:3px solid var(--night)}

/* section titles */
.section-title{position:absolute;left:0;width:1200px;text-align:center;font-family:"Questrial",sans-serif;font-size:30px;font-weight:700}
.divider{position:absolute;left:367px;width:465px;height:1px;background:#c8c8c8}
.divider::after{content:"";position:absolute;left:217px;top:-15px;width:30px;height:30px;border-radius:50%;background:var(--brand)}

/* intro */
.intro{position:absolute;left:0;top:643px;width:1200px;height:304px;background:var(--paper)}
.intro p{position:absolute;left:0;width:1200px;text-align:center;font-size:16.5px;line-height:29.5px;color:var(--ink)}
.intro strong{font-weight:900}

/* offers */
.offers-photo{position:absolute;left:0;top:947px;width:1200px;height:548px;background:linear-gradient(90deg,#3b3a38 0%,#4d463f 45%,#5a4a3e 75%,#3f352e 100%)}
.offers .section-title{color:var(--white)}
.offers .divider{background:rgba(255,255,255,.4)}
.loan-card{position:absolute;top:1099px;width:203px;height:314px;background:var(--white);text-align:center}
.loan-card .card-image{position:absolute;left:14px;top:16px;width:175px;height:122px}
.loan-card h3{position:absolute;left:0;top:155px;width:203px;font-weight:700;font-size:21px;color:var(--brand);letter-spacing:.5px}
.loan-card p{position:absolute;left:12px;top:192px;width:179px;font-size:12.5px;line-height:18px;color:#333}
.btn-more{position:absolute;left:44px;top:265px;width:115px;height:28px;border:1.5px solid var(--brand-dark);font-weight:700;font-size:12px;color:var(--brand);display:flex;align-items:center;justify-content:center}

/* repayments */
.repay h2{position:absolute;left:163px;top:1543px;font-weight:700;font-size:40px;color:var(--brand)}
.repay p{position:absolute;left:163px;top:1601px;font-weight:700;font-size:19px;color:#333}
.btn-calc{position:absolute;left:807px;top:1556px;width:195px;height:51px;background:var(--brand);color:var(--white);font-weight:700;font-size:17px;letter-spacing:.5px;display:flex;align-items:center;justify-content:center;border-left:3px solid var(--night);border-right:3px solid var(--night)}

/* guarantee band */
.guarantee-photo{position:absolute;left:0;top:1684px;width:1200px;height:188px;background:linear-gradient(90deg,#6b4a34 0%,#4c4440 20%,#3c3b3b 60%,#2e2e30 100%)}
.guarantee h2{position:absolute;left:163px;top:1735px;font-size:26px;font-weight:400;color:var(--white)}
.guarantee p{position:absolute;left:163px;top:1790px;font-size:19px;font-weight:700;color:var(--white)}
.btn-find{position:absolute;left:807px;top:1752px;width:195px;height:52px;background:var(--pale);color:var(--brand);font-weight:700;font-size:17px;letter-spacing:.5px;display:flex;align-items:center;justify-content:center;border-left:3px solid var(--brand);border-right:3px solid var(--brand)}

/* footer */
.site-footer{position:absolute;left:0;top:1872px;width:1200px;height:311px;background:var(--brand);color:var(--white)}
.footer-col{position:absolute;top:24px}
.footer-col h4{font-weight:400;font-size:18px;letter-spacing:1px;text-transform:uppercase;padding-bottom:8px;border-bottom:1px solid rgba(255,255,255,.25);display:inline-block}
.footer-links{list-style:none;margin-top:12px}
.footer-links li{font-size:14.5px;line-height:30.6px;padding-left:14px;position:relative}
.footer-links li::before{content:"";position:absolute;left:0;top:12px;border-left:5px solid var(--white);border-top:4px solid transparent;border-bottom:4px solid transparent}
.footer-links li.is-current{color:#e2a77f}
.contact-row{display:flex;gap:16px;font-size:14.5px;line-height:21px;margin-top:16px;align-items:flex-start}
.contact-row svg{flex:none;margin-top:2px}
.social-row{display:flex;align-items:center;gap:14px;font-size:14.5px;margin-top:21px}
.social-row span.tile{width:24px;height:24px;border-radius:3px;background:#2f5f9e}
.social-row span.tile.warm{background:#d3503c}
.social-row span.tile.sky{background:#2aa3e0}
.footer-disc{position:absolute;left:866px;top:62px;width:172px;height:172px;border-radius:50%;background:rgba(255,255,255,.18)}
.copyright{position:absolute;left:0;top:2183px;width:1200px;height:45px;background:var(--night);color:var(--white);font-size:13px;display:flex;align-items:center;justify-content:center}
</style>
</head>
<body>

<header class="site-header">
  <div class="brand"><span class="brand-mark"></span><span class="brand-name">BRIGHTPATH FINANCE</span></div>
  <div class="btn-apply">APPLY NOW</div>
  <div class="header-phone">
    <svg width="20" height="20" viewBox="0 0 24 24" aria-hidden="true"><path fill="#2b2b2b" d="M6.6 10.8a15 15 0 0 0 6.6 6.6l2.2-2.2c.3-.3.7-.4 1-.2 1.1.4 2.3.6 3.6.6.6 0 1 .4 1 1V20c0 .6-.4 1-1 1A17 17 0 0 1 3 4c0-.6.4-1 1-1h3.5c.6 0 1 .4 1 1 0 1.3.2 2.5.6 3.6.1.3 0 .7-.2 1z"/></svg>
    123-456-7890
  </div>
</header>

<nav class="main-nav">
  <ul>
    <li class="is-active">Home</li><li>About Us</li><li>Vehicle Loans</li><li>Other Loans</li><li>Insurance</li><li>Finance Calculator</li><li>Contact Us</li>
  </ul>
</nav>

<section class="hero">
  <div class="hero-photo" role="img" aria-label="Photo of a smiling young family of four outside their home"></div>
  <div class="rate-seal" aria-hidden="true"></div>
  <ul class="feature-list">
    <li><svg width="18" height="14" viewBox="0 0 18 14"><path d="M1 7l5 5L17 1" fill="none" stroke="#111" stroke-width="3"/></svg>Low rate car loans from 4.69%<br>comparison rate 4.99%*</li>
    <li><svg width="18" height="14" viewBox="0 0 18 14"><path d="M1 7l5 5L17 1" fill="none" stroke="#111" stroke-width="3"/></svg>Low fees</li>
    <li><svg width="18" height="14" viewBox="0 0 18 14"><path d="M1 7l5 5L17 1" fill="none" stroke="#111" stroke-width="3"/></svg>Low total cost loans</li>
  </ul>
  <form class="quote-panel">
    <div class="quote-title">QUICK &amp; EASY QUOTE</div>
    <div class="quote-field" style="top:93px">First Name*</div>
    <div class="quote-field" style="top:151px">Last Name*</div>
    <div class="quote-field" style="top:209px">Email Address*</div>
    <div class="quote-field" style="top:267px">Phone Number*</div>
    <div class="quote-field" style="top:325px">Loan Amount in dollars *</div>
    <div class="quote-terms"><span class="box"></span>I agree to the <em>Terms &amp; Conditions</em></div>
    <div class="btn-quote">GET MY BEST RATE NOW</div>
  </form>
</section>

<section class="intro">
  <h2 class="section-title" style="top:33px">Online Loan Pre Approval</h2>
  <div class="divider" style="top:100px"></div>
  <p style="top:138px">Complete our short online application to get finance for your car, truck, motorbike, equipment, boat or caravan!<br>
  We have helped thousands of Australians obtain the finance they need to buy a new or used vehicle.<br>
  <strong>We'll find you competitive vehicle finance that'll get you on the road fast and if you've had credit issues in the past,<br>
  we also have access to specialist lenders who could help.</strong></p>
</section>

<section class="offers">
  <div class="offers-photo" role="img" aria-label="Dimmed photo of a family in front of a brick house at dusk"></div>
  <h2 class="section-title" style="top:978px">We Offer Loans For</h2>
  <div class="divider" style="top:1043px"></div>

  <article class="loan-card" style="left:161px">
    <div class="card-image" role="img" aria-label="Photo of a couple buying a car at a dealership" style="background:linear-gradient(135deg,#d9dde2,#8f99a5)"></div>
    <h3>Vehicle Loans</h3>
    <p>Lorem ipsum dolor sit amet,<br>consectetur adipiscing elit.<br>Integer vitae interdum mi</p>
    <div class="btn-more">Read More</div>
  </article>
  <article class="loan-card" style="left:385px">
    <div class="card-image" role="img" aria-label="Photo of a white motor yacht on blue water" style="background:linear-gradient(180deg,#2f7fd0,#0d4b8f)"></div>
    <h3>Boat Loans</h3>
    <p>Lorem ipsum dolor sit amet,<br>consectetur adipiscing elit.<br>Integer vitae interdum mi</p>
    <div class="btn-more">Read More</div>
  </article>
  <article class="loan-card" style="left:609px">
    <div class="card-image" role="img" aria-label="Photo of a model house on top of building plans" style="background:linear-gradient(135deg,#e2d7c4,#b86a3c)"></div>
    <h3>Home Loans</h3>
    <p>Lorem ipsum dolor sit amet,<br>consectetur adipiscing elit.<br>Integer vitae interdum mi</p>
    <div class="btn-more">Read More</div>
  </article>
  <article class="loan-card" style="left:834px">
    <div class="card-image" role="img" aria-label="Photo of a couple meeting a loan adviser" style="background:linear-gradient(135deg,#eef0f2,#6d5a4f)"></div>
    <h3>Personal Loans</h3>
    <p>Lorem ipsum dolor sit amet,<br>consectetur adipiscing elit.<br>Integer vitae interdum mi</p>
    <div class="btn-more">Read More</div>
  </article>
</section>

<section class="repay">
  <h2>What will my repayments be?</h2>
  <p>See how much you could borrow with our loan calculator.</p>
  <div class="btn-calc">LOAN CALCULATOR</div>
</section>

<section class="guarantee">
  <div class="guarantee-photo" role="img" aria-label="Blurred photo of a small model house on coins"></div>
  <h2>Find out what Guaranteed Approval actually means</h2>
  <p>We explain what it means and what we offer instead.</p>
  <div class="btn-find">FIND OUT MORE</div>
</section>

<footer class="site-footer">
  <div class="footer-col" style="left:163px">
    <h4>Quick Links</h4>
    <ul class="footer-links">
      <li class="is-current">Home</li><li>About Us</li><li>Vehicle Loans</li><li>Other Loans</li><li>Insurance</li><li>Finance Calculator</li><li>Contact us</li>
    </ul>
  </div>
  <div class="footer-col" style="left:377px">
    <h4>Contact Details</h4>
    <div class="contact-row"><svg width="16" height="22" viewBox="0 0 16 22"><path d="M8 0a8 8 0 0 1 8 8c0 6-8 14-8 14S0 14 0 8a8 8 0 0 1 8-8z" fill="#cedeed"/><circle cx="8" cy="8" r="3" fill="#0255a3"/></svg><span>Company Name<br>Street Name, City Name<br>State Name - 123456</span></div>
    <div class="contact-row" style="margin-top:22px"><svg width="16" height="16" viewBox="0 0 24 24"><path fill="#cedeed" d="M6.6 10.8a15 15 0 0 0 6.6 6.6l2.2-2.2c.3-.3.7-.4 1-.2 1.1.4 2.3.6 3.6.6.6 0 1 .4 1 1V20c0 .6-.4 1-1 1A17 17 0 0 1 3 4c0-.6.4-1 1-1h3.5c.6 0 1 .4 1 1 0 1.3.2 2.5.6 3.6.1.3 0 .7-.2 1z"/></svg><span>123-456-7890</span></div>
    <div class="contact-row" style="margin-top:22px"><svg width="18" height="16" viewBox="0 0 18 16"><rect x="4" y="0" width="10" height="4" fill="#cedeed"/><rect x="0" y="5" width="18" height="7" rx="1" fill="#cedeed"/><rect x="4" y="10" width="10" height="6" fill="#cedeed" stroke="#0255a3"/></svg><span>123-456-7890</span></div>
    <div class="contact-row" style="margin-top:22px"><svg width="16" height="12" viewBox="0 0 16 12"><rect width="16" height="12" fill="#cedeed"/><path d="M0 0l8 6 8-6" fill="none" stroke="#0255a3" stroke-width="1.5"/></svg><span>info@brightpathfinance.example.com</span></div>
  </div>
  <div class="footer-col" style="left:673px">
    <h4>Follow Us</h4>
    <div class="social-row" style="margin-top:16px"><span class="tile"></span>Friendnest</div>
    <div class="social-row"><span class="tile sky"></span>Chirpline</div>
    <div class="social-row"><span class="tile"></span>Workroll</div>
    <div class="social-row"><span class="tile warm"></span>Circleplus</div>
  </div>
  <div class="footer-disc" aria-hidden="true"></div>
</footer>

<div class="copyright">Copyright © 2016&nbsp; Brightpath Finance. All Right Reserved</div>

</body>
</html>
```